New Zealand Marlborough Sauvignon Blanc wine packaging design

We need packaging design for our new wine brand, Dunmore Vale. The wine is a New Zealand Marlborough Sauvignon Blanc. We would like the packaging will portray elegance and style with an understated label. We are looking for a label that portrays the elegance of the French Riviera. The label should be round or pill shaped.
Updates

Industry/Entity Type

Wine

Font styles to use
Serif
Sans Serif

Requirements
Must have
• The words in order of importance: Dunmore Vale, Sauvignon Blanc, Marlborough, New Zealand. It should be fit to the bottle posted in the links
Nice to have
• a pill shape or circular shape
Should not have
• Illustrations of wine bottles, wine glasses, or grapes

```html
<!DOCTYPE html>
<html lang="en">
<head>
<meta charset="utf-8">
<title>Dunmore Vale Sauvignon Blanc Label</title>
<link rel="stylesheet" href="https://fonts.googleapis.com/css2?family=Libre+Baskerville:ital,wght@0,700;1,700&family=Montserrat:wght@500;600;700&display=swap">
<style>
  :root {
    --canvas: #f3f3f1;
    --label-paper: #f6f6f5;
    --label-edge: #dcdcdc;
    --ring-outer: #ffffff;
    --ring-silver: #b9b9b9;
    --ring-silver-light: #d8d8d8;
    --medallion-dark: #1c1b1b;
    --gold: #cf9b45;
    --gold-line: #d6a04c;
    --band-light: #f3ecdb;
    --band-mid: #e6dcc2;
    --band-dark: #c9c0aa;
    --ink: #141414;
    --ink-soft: #3a3a3a;
  }
  html, body {
    margin: 0;
    padding: 0;
    width: 788px;
    height: 1200px;
    overflow: hidden;
    background: var(--canvas);
  }
  .label-art {
    display: block;
    width: 788px;
    height: 1200px;
  }
  .brand-name {
    font-family: "Libre Baskerville", Georgia, serif;
    font-weight: 700;
    font-size: 50px;
    fill: var(--gold);
    letter-spacing: 1px;
  }
  .variety {
    font-family: "Libre Baskerville", Georgia, serif;
    font-style: italic;
    font-weight: 700;
    font-size: 46px;
    fill: var(--ink);
    letter-spacing: 1px;
  }
  .region {
    font-family: "Montserrat", Arial, sans-serif;
    font-weight: 700;
    font-size: 31px;
    fill: var(--ink-soft);
    letter-spacing: 1.5px;
  }
  .country {
    font-family: "Montserrat", Arial, sans-serif;
    font-weight: 500;
    font-size: 32px;
    fill: var(--ink-soft);
    letter-spacing: 1.5px;
  }
  .vintage {
    font-family: "Montserrat", Arial, sans-serif;
    font-weight: 700;
    font-size: 31px;
    fill: var(--ink);
    letter-spacing: 1px;
  }
</style>
</head>
<body>
<svg class="label-art" viewBox="0 0 788 1200" xmlns="http://www.w3.org/2000/svg">
  <defs>
    <linearGradient id="band-fill" x1="0" y1="0" x2="1" y2="0">
      <stop offset="0" stop-color="var(--band-mid)"/>
      <stop offset="0.35" stop-color="var(--band-light)"/>
      <stop offset="0.75" stop-color="var(--band-mid)"/>
      <stop offset="1" stop-color="var(--band-dark)"/>
    </linearGradient>
    <linearGradient id="silver-ring" x1="0" y1="0" x2="0" y2="1">
      <stop offset="0" stop-color="var(--ring-silver-light)"/>
      <stop offset="1" stop-color="var(--ring-silver)"/>
    </linearGradient>
  </defs>

  <!-- label panel -->
  <g class="label-panel">
    <rect x="54" y="330" width="680" height="819" fill="var(--label-paper)" stroke="var(--label-edge)" stroke-width="1"/>
  </g>

  <!-- round medallion -->
  <g class="medallion">
    <circle cx="394" cy="368" r="232" fill="var(--medallion-dark)"/>
    <circle cx="394" cy="368" r="222" fill="var(--ring-outer)"/>
    <circle cx="394" cy="368" r="188" fill="url(#silver-ring)"/>
    <circle cx="394" cy="368" r="166" fill="var(--medallion-dark)"/>
    <rect class="ornament" role="img" aria-label="Small gold scroll ornament" x="344" y="262" width="100" height="22" rx="11" fill="var(--gold)" opacity="0.55"/>
    <text class="brand-name" x="394" y="360" text-anchor="middle">DUNMORE</text>
    <text class="brand-name" x="394" y="418" text-anchor="middle">VALE</text>
    <rect class="ornament" role="img" aria-label="Small gold scroll ornament" x="344" y="452" width="100" height="22" rx="11" fill="var(--gold)" opacity="0.55"/>
  </g>

  <!-- variety band -->
  <g class="variety-band">
    <rect x="54" y="676" width="680" height="200" fill="url(#band-fill)"/>
    <line x1="54" y1="676" x2="734" y2="676" stroke="var(--gold-line)" stroke-width="4"/>
    <line x1="54" y1="688" x2="734" y2="688" stroke="var(--gold-line)" stroke-width="1.5"/>
    <line x1="54" y1="864" x2="734" y2="864" stroke="var(--gold-line)" stroke-width="1.5"/>
    <line x1="54" y1="876" x2="734" y2="876" stroke="var(--gold-line)" stroke-width="4"/>
    <text class="variety" x="394" y="770" text-anchor="middle">Sauvignon Blanc</text>
    <text class="region" x="394" y="830" text-anchor="middle">MARLBOROUGH</text>
  </g>

  <!-- origin and vintage -->
  <text class="country" x="394" y="990" text-anchor="middle">NEW ZEALAND</text>
  <text class="vintage" x="394" y="1098" text-anchor="middle">2023</text>
</svg>
</body>
</html>
```